we are an outdoor outlet in a country club that has a variety of outlets. The Club is called Meadowlark and is located in Cairo, Egypt. This garden menu will include cuisines from the Mediterranean, Asia and Texmex. we need a menu that is colorful and would fit an A3 size, back and front are to be used. Attached is the old menu currently in use (Garden Menu 2012.pdf is just for reference) and the new menu text for you to use is under the name Garden Menu Fall 2013
thank you.
Updates
Logo files have been uploaded for this project
Industry/Entity Type
Club
Look and feel
Each slider illustrates characteristics of the customer's brand and the style your logo design should communicate.

```html
<!DOCTYPE html>
<html lang="en">
<head>
<meta charset="utf-8">
<title>Garden Menu – Meadowlark</title>
<link rel="stylesheet" href="https://fonts.googleapis.com/css2?family=Josefin+Sans:wght@700&family=Great+Vibes&family=Oswald:wght@500&family=Crimson+Text:ital@1&family=Quicksand:wght@500&display=swap">
<style>
:root{
  --backdrop:#76763f;
  --paper:#f2ede1;
  --brown:#5b3518;
  --lime:#b7d42a;
  --lime-light:#d3e85a;
  --orange:#d6531f;
  --cream-text:#fbe9d8;
}
*{margin:0;padding:0;box-sizing:border-box}
html,body{width:1200px;height:1000px;overflow:hidden;background:var(--backdrop)}
.menu{position:absolute;left:256px;top:14px;width:688px;height:973px;background:var(--paper);box-shadow:0 4px 18px rgba(0,0,0,.35);color:var(--brown);overflow:hidden}
.frame{position:absolute;left:41px;top:46px;width:605px;height:887px;border:3px solid var(--lime)}
.frame::after{content:"";position:absolute;inset:5px;border:1px dashed #cfc6a8}
.banner{position:absolute;left:50px;top:50px;width:588px;height:84px;background:linear-gradient(180deg,var(--lime-light),var(--lime));display:flex;align-items:center;padding:0 16px 0 22px}
.banner-title{font-family:"Josefin Sans",sans-serif;font-weight:700;font-size:50px;line-height:1;color:#fff;letter-spacing:1px;white-space:nowrap;margin-top:8px}
.brand{margin-left:auto;display:flex;align-items:center;gap:8px;font-family:"Quicksand",sans-serif;font-weight:500;font-size:26px;color:#fff;white-space:nowrap}
.brand-dot{width:26px;height:26px;border-radius:50%;background:#fff;flex:none}
.script{font-family:"Great Vibes",cursive;color:var(--brown);font-weight:400}
.corner-title{position:absolute;left:0;width:688px;top:166px;text-align:center;font-size:36px}
.rule{position:absolute;height:1px;background:#a9a079}
.leaf{position:absolute;width:14px;height:14px;background:var(--lime);border-radius:50% 0 50% 0}
.soups-label{position:absolute;left:118px;top:248px;font-size:28px}
.soup{position:absolute;top:252px;width:130px;text-align:center}
.name{font-family:"Oswald",sans-serif;font-weight:500;font-size:10px;text-transform:uppercase;letter-spacing:.2px;display:block;line-height:12px;white-space:nowrap}
.desc{font-family:"Crimson Text",serif;font-style:italic;font-size:8px;line-height:9px;display:block}
.col{position:absolute;text-align:center}
.heading{font-size:26px;line-height:28px}
.sub{font-family:"Crimson Text",serif;font-style:italic;font-size:8px;font-weight:700;display:block}
.item{margin-top:6px}
.small .name{font-size:7px}
.spaced{font-family:"Oswald",sans-serif;font-size:7px;letter-spacing:3px;text-transform:uppercase;margin-right:6px}
.opts{font-family:"Crimson Text",serif;font-style:italic;font-size:8px;line-height:10px}
.mains{position:absolute;left:301px;top:680px;width:305px;height:230px;background:var(--orange);border-radius:12px;color:var(--cream-text);text-align:center;padding-top:14px}
.mains::before{content:"";position:absolute;inset:5px;border:1px dashed rgba(255,255,255,.7);border-radius:9px}
.mains .heading{color:#fff}
.mains .item{margin-top:8px}
.mains .name{color:#fff}
.photo{position:absolute}
.photo-sandwich{left:0;top:326px;width:132px;height:136px;background:linear-gradient(135deg,#e7c58a,#c98b4b 55%,#f2efe6);border-radius:0 8px 8px 0}
.photo-pizza{left:513px;top:622px;width:176px;height:112px;border-radius:50%;background:radial-gradient(circle,#d9472c 35%,#e6b672 70%,#c98d4a)}
.note{position:absolute;left:13px;top:878px;width:80px;height:80px;border-radius:50%;background:var(--lime);border:3px solid #e2ef9c;color:#fff;font-family:"Oswald",sans-serif;font-size:6.5px;text-align:center;display:flex;align-items:center;justify-content:center;padding:12px;line-height:8px;text-transform:uppercase}
</style>
</head>
<body>
<main class="menu">
  <div class="frame"></div>
  <header class="banner">
    <h1 class="banner-title">GARDEN MENU</h1>
    <div class="brand"><span class="brand-dot"></span>Meadowlark</div>
  </header>

  <h2 class="script corner-title">Mediterranean Corner</h2>
  <div class="rule" style="left:190px;top:214px;width:306px"></div>
  <div class="leaf" role="img" aria-label="leaf ornament" style="left:336px;top:206px"></div>

  <h3 class="script soups-label">Soups</h3>
  <div class="soup" style="left:190px"><span class="name">Tomato Basil | L.E 00.00</span><span class="desc">Simmered tomato soup finished with fresh basil and cream</span></div>
  <div class="soup" style="left:318px"><span class="name">Chicken Cream | L.E 00.00</span><span class="desc">Chicken broth with roasted chicken cubes, pine nuts, and cream</span></div>
  <div class="soup" style="left:455px"><span class="name">Moroccan Harira | L.E 00.00</span><span class="desc">Vegetable broth with fresh tomato, chickpeas, lentil, cilantro, and diced lamb</span></div>

  <div class="photo photo-sandwich" role="img" aria-label="Photo of a club sandwich on a plate"></div>

  <section class="col small" style="left:140px;top:312px;width:150px">
    <h3 class="script heading">Sandwiches</h3>
    <span class="sub">(Served with French fries or a garden salad)</span>
    <div class="leaf" role="img" aria-label="leaf ornament" style="position:relative;margin:3px auto 0"></div>
    <div class="item"><span class="name">Beef or Chicken Shawerma | L.E 00.00</span></div>
    <div class="item"><span class="name">Grilled Kofta | L.E 00.00</span></div>
    <div class="item"><span class="name">Greek Lamb Gyro | L.E 00.00</span><span class="desc">in pita bread with Tzatziki</span></div>
    <div class="item"><span class="name">Club Sandwich | L.E 00.00</span><span class="desc">with smoked beef, turkey, egg</span></div>
  </section>

  <section class="col" style="left:104px;top:474px;width:194px">
    <h3 class="script heading">Appetizers</h3>
    <div class="leaf" role="img" aria-label="leaf ornament" style="position:relative;margin:2px auto 0"></div>
    <div class="item"><span class="name">Salmon Tartare | L.E. 00.00</span><span class="desc">seasoned with lemon juice, garlic, and crushed black pepper</span></div>
    <div class="item"><span class="name">Roasted Eggplant Rolls | L.E. 00.00</span><span class="desc">with herbed ricotta cheese and pine nuts</span></div>
    <div class="item"><span class="name">Falafel in Mini Pita | L.E. 00.00</span><span class="desc">served with tehina and oriental salsa</span></div>
    <div class="item"><span class="name">Mankousha | L.E. 00.00</span><span class="desc">with thyme and olive oil</span></div>
    <div class="item"><span class="name">Fried Kobeba | L.E. 00.00</span><span class="desc">with minced meat, spices, and pine nuts</span></div>
    <div class="item"><span class="name">Fried Calamari a la Romana | L.E. 00.00</span><span class="desc">served with aioli</span></div>
    <div class="item"><span class="name">Samboussek | L.E. 00.00</span><span class="desc">with herbed white cheese and mint</span></div>
    <div class="item"><span class="name">Oriental Sausage Sautéed | L.E. 00.00</span><span class="desc">with garlic and onion</span></div>
    <div class="item"><span class="name">Mini Vine Leaves | L.E. 00.00</span><span class="desc">with a yoghurt dip</span></div>
    <div class="item"><span class="name">Fatouch | L.E. 00.00</span><span class="desc">with a pomegranate syrup dressing</span></div>
    <div class="item"><span class="name">Hummus | L.E. 00.00</span><span class="desc">seasoned with lemon juice, garlic, and olive oil</span></div>
    <div class="item"><span class="name">White Cheese | L.E. 00.00</span><span class="desc">with diced tomato, thyme, and olive oil</span></div>
    <div class="item"><span class="name">Tehina | L.E. 00.00</span><span class="desc">seasoned with cumin, lemon juice, and garlic</span></div>
  </section>

  <section class="col" style="left:313px;top:304px;width:260px">
    <h3 class="script heading">Salads</h3>
    <div class="leaf" role="img" aria-label="leaf ornament" style="position:relative;margin:2px auto 0"></div>
    <div class="item"><span class="name">Caprese | L.E. 00.00</span><span class="desc">Buffalo mozzarella and sliced tomato with a balsamic vinaigrette</span></div>
    <div class="item"><span class="name">Rocket Apple | L.E. 00.00</span><span class="desc">Rocket leaves with gorgonzola, croutons, and strawberry vinaigrette</span></div>
    <div class="item"><span class="name">French Riviera Nicoise | L.E. 00.00</span><span class="desc">Lettuce, egg, tomato, tuna, olives, onion, celery, radish, bell pepper in a French vinaigrette</span></div>
    <div class="item"><span class="name">Folle | L.E. 00.00</span><span class="desc">Mixed greens with crab sticks, mushroom, corn, cherry tomato in a mango vinaigrette</span></div>
  </section>

  <section class="col" style="left:313px;top:490px;width:260px">
    <h3 class="script heading">Pizza &amp; Pasta</h3>
    <div class="leaf" role="img" aria-label="leaf ornament" style="position:relative;margin:2px auto 0"></div>
    <div class="item"><span class="name">Pizza Margarita | L.E. 00.00</span><span class="desc">(Choose your toppings)</span></div>
    <div class="item"><span class="spaced">Toppings</span></div>
    <div class="opts">Bell Peppers | Olives | Tomato | Onion | Mushroom<br>Chicken | Tuna | Pepperoni | Smoked Salmon | Shrimps</div>
    <div class="item"><span class="name">Create Your Own Pasta | L.E. 00.00</span></div>
    <div class="opts" style="margin-top:6px"><span class="spaced">Type</span>Spaghetti | Tagliatelle | Penne</div>
    <div class="opts" style="margin-top:6px"><span class="spaced">Sauces</span>Napolitana | Bolognese | Alfredo</div>
    <div class="item"><span class="name">Lasagna | L.E. 00.00</span></div>
  </section>

  <section class="mains">
    <h3 class="script heading" style="position:relative">Main Courses</h3>
    <div class="item"><span class="name">Veal Parmeggiana | L.E. 00.00</span><span class="desc">Breaded veal escalope topped with melted cheese and tomato sauce served with Spaghetti</span></div>
    <div class="item"><span class="name">Chicken a la Francaise | L.E. 00.00</span><span class="desc">Pan fried chicken breast in a mushroom cream sauce with vegetables white rice</span></div>
    <div class="item"><span class="name">Grilled Salmon | L.E. 00.00</span><span class="desc">Salmon steak charcoal grilled with avocado tomato relish and creamy mushroom risotto</span></div>
    <div class="item"><span class="name">Moroccan Chicken | L.E. 00.00</span><span class="desc">Chicken cubes simmered with spices and olives served with tomato rice</span></div>
    <div class="item"><span class="name">Filet | L.E. 00.00</span><span class="desc">Tender filet grilled to your liking served with mashed potato and creamed spinach</span></div>
    <div class="item"><span class="name" style="font-size:7px">Choice of Sauces</span><span class="desc">Brown Mushroom | Green Peppercorn | Gorgonzola</span></div>
  </section>

  <div class="photo photo-pizza" role="img" aria-label="Photo of a margherita pizza with basil and olives"></div>

  <div class="note">Prices are subject to 12% service charge and 10% sales tax</div>
</main>
</body>
</html>
```